New Business Card Design Project

I need a design for business cards, i am an electrical business called "Corvane Electrical and Communications" i need the cards to be double sided with the company logo on the back (attached) the front needs to say my company name, web site, email address, telephone number, and ABN number and electrical license number. I am open to different arrangements of the information but would like the background to be incorporating something electrical or something that looks smart. open to all additional ideas also.

The company colours are orange and grey see logo attached.

Business Name: Corvane Electrical and Communications
Website: corvaneelectricalandcomms.example.com.au
Email: brent@corvaneelectricalandcomms.example.com.au
Telephone(mobile): 0481209736
ABN: 71208349162
Lic No: 418273D

Target Market(s)

Business entities, Project Managers, Accounts, Clients

Industry/Entity Type

Electrician

Contact Information for Business Card

I need a design for business cards, i am an electrical business called "Corvane Electrical and Communications" i need the cards to be double sided with the company logo on the back (attached) the front needs to say my company name

Font styles to use
Serif
Sans Serif

Colors
f37122
5c5c5c

Requirements
Must have
• Must have the Logo on the back open to different ways of it being on the back but had in mind to keep it central but again open to other options
Nice to have
• A real modern cool background that is eye catching yet contemporary
Should not have
• No backgrounds of a light bulb or plug or anything like that

```html
<!DOCTYPE html>
<html lang="en">
<head>
<meta charset="utf-8">
<title>Corvane Electrical and Communications – Business Card</title>
<link rel="stylesheet" href="https://fonts.googleapis.com/css2?family=Exo+2:wght@500;600;700&family=Arimo:wght@400;700&display=swap">
<style>
  :root {
    --page: #2f2f30;
    --card-grey: #5a5b5d;
    --orange: #f9ac18;
    --white: #ffffff;
    --ink: #3a3a3c;
  }
  * { margin: 0; padding: 0; box-sizing: border-box; }
  html, body {
    width: 1105px;
    height: 1200px;
    overflow: hidden;
    background: var(--page);
  }
  .sheet {
    position: relative;
    width: 1105px;
    height: 1200px;
  }
  .card {
    position: absolute;
    left: 196px;
    width: 720px;
    height: 410px;
    background: var(--card-grey);
    overflow: hidden;
  }
  .card--front { top: 146px; }
  .card--back { top: 602px; }

  .brand {
    position: absolute;
    left: 36px;
    top: 52px;
    font-family: "Exo 2", sans-serif;
    font-weight: 600;
    color: var(--white);
  }
  .brand__name {
    display: block;
    font-size: 60px;
    line-height: 1;
    letter-spacing: 6px;
    text-transform: uppercase;
  }
  .brand__descriptor {
    display: block;
    margin-top: 8px;
    font-size: 15.5px;
    letter-spacing: 1.2px;
    text-transform: uppercase;
  }

  .holder {
    position: absolute;
    right: 35px;
    top: 66px;
    text-align: right;
    font-family: "Exo 2", sans-serif;
    font-weight: 700;
  }
  .holder__name {
    display: block;
    font-size: 27px;
    color: var(--orange);
    line-height: 1.1;
  }
  .holder__title {
    display: block;
    font-size: 19px;
    color: var(--white);
    margin-top: 2px;
  }

  .energy-band {
    position: absolute;
    left: 0;
    top: 160px;
    width: 720px;
    height: 250px;
    background: linear-gradient(to bottom, rgba(249,172,24,0) 0%, rgba(249,172,24,0.55) 30%, var(--orange) 55%, var(--orange) 100%);
  }

  .contact {
    position: absolute;
    font-family: Arimo, sans-serif;
    color: var(--ink);
  }
  .contact--left { left: 36px; top: 312px; }
  .contact--right { right: 35px; top: 340px; text-align: right; }
  .contact__line {
    display: block;
    font-size: 16px;
    line-height: 28px;
  }
  .contact__line--mobile { font-size: 18px; line-height: 30px; }
  .contact__label { font-weight: 700; }
  .contact--right .contact__line { font-size: 19px; line-height: 28px; }

  .card--back .brand {
    left: 0;
    right: 0;
    top: 150px;
    text-align: center;
  }
  .card--back .brand__name {
    font-size: 84px;
    letter-spacing: 9px;
  }
  .card--back .brand__descriptor {
    margin-top: 12px;
    font-size: 19px;
    letter-spacing: 1.6px;
  }
</style>
</head>
<body>
<main class="sheet">
  <section class="card card--front" aria-label="Business card front">
    <div class="energy-band" role="img" aria-label="Orange electrical wave band rising across the card"></div>
    <div class="brand">
      <span class="brand__name">Corvane</span>
      <span class="brand__descriptor">Electrical &amp; Communications</span>
    </div>
    <div class="holder">
      <span class="holder__name">Dana Whitlow</span>
      <span class="holder__title">CEO/Founder</span>
    </div>
    <div class="contact contact--left">
      <span class="contact__line contact__line--mobile"><span class="contact__label">Mobile :</span> 0481209736</span>
      <span class="contact__line">brent@corvaneelectricalandcomms.example.com.au</span>
      <span class="contact__line">corvaneelectricalandcomms.example.com.au</span>
    </div>
    <div class="contact contact--right">
      <span class="contact__line">ABN: 71208349162</span>
      <span class="contact__line">Lic No: 418273D</span>
    </div>
  </section>

  <section class="card card--back" aria-label="Business card back">
    <div class="brand">
      <span class="brand__name">Corvane</span>
      <span class="brand__descriptor">Electrical &amp; Communications</span>
    </div>
  </section>
</main>
</body>
</html>
```